Business Card Design Can you design a business card design? Looking for something unique and differe

Can you design a business card design? Looking for something unique and different. Can you design a business card design? Looking for something unique and different.Can you design a business card design? Looking for something unique and different.Can you design a business card design? Looking for something unique and different.Can you design a business card design? Looking for something unique and different.Can you design a business card design? Looking for something unique and different.

Industry/Entity Type

Business

Contact Information for Business Card

Can you design a business card design? Looking for something unique and different.

Font styles to use
Serif

```html
<!DOCTYPE html>
<html lang="en">
<head>
<meta charset="utf-8">
<title>Business Card</title>
<link rel="stylesheet" href="https://fonts.googleapis.com/css2?family=Quicksand:wght@600;700&family=Open+Sans:ital,wght@0,400;1,400&display=swap">
<style>
  :root {
    --backdrop: #d8d3ce;
    --card: #eeebe8;
    --card-edge: #f7f5f3;
    --accent: #654a78;
    --ink: #1e1e22;
    --icon: #4a4a50;
  }
  * { margin: 0; padding: 0; box-sizing: border-box; }
  html, body {
    width: 1200px; height: 970px; overflow: hidden;
    background: var(--backdrop);
  }
  .business-card {
    position: absolute;
    left: 100px; top: 207px;
    width: 1000px; height: 556px;
    background: linear-gradient(160deg, var(--card-edge) 0%, var(--card) 60%, #e6e2de 100%);
    border: 1px solid #faf9f8;
    box-shadow: 0 14px 40px rgba(60, 50, 45, 0.18);
    font-family: "Open Sans", Arial, sans-serif;
    color: var(--ink);
  }
  .holder-name {
    position: absolute; left: 44px; top: 56px;
    font-family: "Quicksand", Verdana, sans-serif;
    font-weight: 700; font-size: 31px; color: var(--accent);
    letter-spacing: 0.2px;
  }
  .holder-title {
    position: absolute; left: 45px; top: 98px;
    font-style: italic; font-size: 18px;
  }
  .office-address {
    position: absolute; left: 45px; top: 322px;
    font-size: 22px; line-height: 34px;
  }
  .contact-list {
    position: absolute; left: 45px; top: 406px;
    list-style: none; font-size: 21px;
  }
  .contact-list li {
    display: flex; align-items: center;
    height: 34px;
  }
  .contact-list svg {
    width: 20px; height: 20px; margin: 0 27px 0 2px;
    fill: var(--icon);
  }
  .brand-name {
    position: absolute; left: 560px; top: 408px;
    width: 400px; text-align: center;
    font-family: "Quicksand", Verdana, sans-serif;
    font-weight: 700; font-size: 54px; color: var(--accent);
  }
</style>
</head>
<body>
  <section class="business-card">
    <h1 class="holder-name">Your Long Name</h1>
    <p class="holder-title">Managing Director</p>

    <p class="office-address">Your Commercial or office address<br>in just two line with pincode</p>

    <ul class="contact-list">
      <li>
        <svg viewBox="0 0 20 20" aria-hidden="true"><path d="M2 6c0-2 3-3 8-3s8 1 8 3v2h-4V6.5c-1-.5-2.5-.7-4-.7s-3 .2-4 .7V8H2z"/><path d="M5 9h10l2 8H3z"/></svg>
        00.00.00.0000
      </li>
      <li>
        <svg viewBox="0 0 20 20" aria-hidden="true"><path d="M1 4h18v1l-9 6-9-6z"/><path d="M1 7l9 6 9-6v9H1z"/></svg>
        yourname@yourwebsite.com
      </li>
      <li>
        <svg viewBox="0 0 20 20" aria-hidden="true"><path d="M10 1a9 9 0 1 0 0 18 9 9 0 0 0 0-18zm0 2c1 0 2 2 2.4 5H7.6C8 5 9 3 10 3zM3.2 8h2.6a17 17 0 0 0 0 4H3.2a7 7 0 0 1 0-4zm4.4 4a15 15 0 0 1 0-4h4.8a15 15 0 0 1 0 4zm6.6 0a17 17 0 0 0 0-4h2.6a7 7 0 0 1 0 4zM10 17c-1 0-2-2-2.4-5h4.8C12 15 11 17 10 17z"/></svg>
        www.yourwebsite.com
      </li>
    </ul>

    <p class="brand-name">Dosewell</p>
  </section>
</body>
</html>
```